Business Card Design Can you design a business card design? Looking for something unique and differe

Can you design a business card design? Looking for something unique and different. Can you design a business card design? Looking for something unique and different.Can you design a business card design? Looking for something unique and different.Can you design a business card design? Looking for something unique and different.Can you design a business card design? Looking for something unique and different.Can you design a business card design? Looking for something unique and different.

Industry/Entity Type

Business

Contact Information for Business Card

Can you design a business card design? Looking for something unique and different.

Font styles to use
Serif

```html
<!DOCTYPE html>
<html lang="en">
<head>
<meta charset="utf-8">
<title>Business Card – Front and Back</title>
<link href="https://fonts.googleapis.com/css2?family=Open+Sans:ital,wght@0,400;0,600;1,400&display=swap" rel="stylesheet">
<style>
  :root {
    --backdrop: #d9d9d9;
    --card: #ffffff;
    --brand-purple: #8a6d9f;
    --ink: #222222;
    --muted-grey: #6e6e6e;
    --edge-black: #101010;
  }
  * { box-sizing: border-box; margin: 0; padding: 0; }
  html, body {
    width: 1200px;
    height: 852px;
    overflow: hidden;
    background: var(--backdrop);
    font-family: "Open Sans", Arial, sans-serif;
  }
  .stage {
    position: relative;
    width: 1200px;
    height: 852px;
  }
  .card {
    position: absolute;
    width: 525px;
    height: 300px;
    background: var(--card);
    border-radius: 14px;
    overflow: hidden;
    box-shadow: 0 6px 18px rgba(0,0,0,0.18);
  }
  .card--front { left: 55px; top: 276px; }
  .card--back  { left: 620px; top: 276px; }

  .wordmark {
    display: flex;
    align-items: center;
    gap: 12px;
    color: var(--brand-purple);
    font-weight: 600;
    letter-spacing: 0.5px;
  }
  .wordmark__square {
    width: 0.8em;
    height: 0.8em;
    background: var(--brand-purple);
  }
  .card--front .wordmark {
    position: absolute;
    left: 0; right: 0; top: 0; bottom: 0;
    justify-content: center;
    font-size: 52px;
  }
  .card--back .wordmark {
    position: absolute;
    right: 34px;
    top: 48px;
    font-size: 38px;
  }

  .holder {
    position: absolute;
    left: 34px;
    top: 84px;
  }
  .holder__name {
    color: var(--brand-purple);
    font-size: 19px;
    font-weight: 600;
  }
  .holder__role {
    color: var(--ink);
    font-size: 11px;
    font-style: italic;
    margin-top: 2px;
    padding-left: 16px;
  }

  .contact {
    position: absolute;
    left: 34px;
    top: 150px;
    list-style: none;
    color: var(--ink);
    font-size: 12.5px;
    line-height: 19px;
  }
  .contact li {
    display: flex;
    align-items: center;
    gap: 10px;
  }
  .contact svg { width: 12px; height: 12px; flex: none; }
  .contact .contact__address {
    align-items: flex-start;
    margin-top: 4px;
    padding-left: 22px;
  }

  .swoosh {
    position: absolute;
    left: 0;
    bottom: 0;
    width: 525px;
    height: 300px;
  }
</style>
</head>
<body>
<main class="stage">

  <section class="card card--front" aria-label="Card front">
    <div class="wordmark">
      <span class="wordmark__square"></span>
      <span class="wordmark__name">Dosewise</span>
    </div>
  </section>

  <section class="card card--back" aria-label="Card back">
    <svg class="swoosh" viewBox="0 0 525 300" aria-hidden="true">
      <path d="M525 150 C470 230 330 280 0 300 L525 300 Z" fill="var(--edge-black)"/>
      <path d="M525 215 C420 260 260 285 0 296 L0 300 L525 300 Z" fill="var(--brand-purple)"/>
    </svg>

    <div class="wordmark">
      <span class="wordmark__square"></span>
      <span class="wordmark__name">Dosewise</span>
    </div>

    <div class="holder">
      <p class="holder__name">Your Long Name</p>
      <p class="holder__role">Managing Director</p>
    </div>

    <ul class="contact">
      <li>
        <svg viewBox="0 0 12 12" aria-hidden="true"><path d="M2 1h3l1 3-2 1a7 7 0 0 0 3 3l1-2 3 1v3c-5 0-9-4-9-9z" fill="var(--brand-purple)"/></svg>
        <span>00.00.00.0000</span>
      </li>
      <li>
        <svg viewBox="0 0 12 12" aria-hidden="true"><rect x="0.5" y="2.5" width="11" height="7" fill="var(--brand-purple)"/><path d="M0.5 2.5 6 7l5.5-4.5" stroke="#fff" fill="none"/></svg>
        <span>yourname@yourwebsite.com</span>
      </li>
      <li>
        <svg viewBox="0 0 12 12" aria-hidden="true"><circle cx="6" cy="6" r="5" fill="none" stroke="var(--brand-purple)" stroke-width="1.4"/><path d="M1 6h10M6 1c-3 3-3 7 0 10M6 1c3 3 3 7 0 10" stroke="var(--brand-purple)" fill="none"/></svg>
        <span>www.yourwebsite.com</span>
      </li>
      <li class="contact__address">
        <span>Your Commercial or office address<br>in just two line with pincode</span>
      </li>
    </ul>
  </section>

</main>
</body>
</html>
```